Business Card Design for company

We want new business cards. We'd like something different-- yet still highly professional. Our tagline is Providing leadership, delivering success. Stock photos are ok, as long as they are relevant and look upscale.

Target Market(s)

Architecture/Business Management Consulting/Engineering Consulting

Contact Information for Business Card

dark gray background with pops of blue might be good, but you tell me. You're the designers. Rounded corners might be nice, but again, you tell me.

Font styles to use
Serif
Sans Serif

Colors
3276b5
5c5c5c
9d9d9d
fbfbfb

Requirements
Nice to have
• Something different, but still very professional.

```html
<!DOCTYPE html>
<html lang="en">
<head>
<meta charset="UTF-8">
<title>Corvane Group – Business Card</title>
<link href="https://fonts.googleapis.com/css2?family=Montserrat:wght@600;700&family=Open+Sans:ital,wght@0,400;1,400&display=swap" rel="stylesheet">
<style>
  :root {
    --brand-blue: #3276b5;
    --brand-gray: #5c5c5c;
    --soft-gray: #9d9d9d;
    --paper: #fbfbfb;
    --backdrop: #e4e6e9;
    --text-dark: #444444;
  }
  * { margin: 0; padding: 0; box-sizing: border-box; }
  html, body {
    width: 1154px; height: 1200px; overflow: hidden;
    background: var(--backdrop);
  }
  .stage {
    width: 1154px; height: 1200px;
    display: flex; flex-direction: column; align-items: center; justify-content: center;
    gap: 44px;
  }
  .card {
    position: relative;
    width: 880px; height: 503px;
    background: var(--paper);
    border-radius: 26px;
    overflow: hidden;
    box-shadow: 0 6px 18px rgba(0,0,0,0.18);
  }
  .card-band { position: absolute; top: 0; left: 0; width: 880px; height: 110px; }

  /* Front */
  .front-brand {
    position: absolute; left: 0; right: 0; top: 215px;
    text-align: center;
    font-family: 'Montserrat', sans-serif; font-weight: 700;
    font-size: 74px; letter-spacing: 2px;
    color: var(--brand-blue);
  }
  .front-web {
    position: absolute; left: 0; right: 0; bottom: 50px;
    text-align: center;
    font-family: 'Montserrat', sans-serif; font-weight: 700;
    font-size: 22px; color: var(--brand-blue); letter-spacing: 0.5px;
  }

  /* Back */
  .tagline {
    position: absolute; left: 40px; top: 92px;
    font-family: 'Montserrat', sans-serif; font-weight: 700;
    font-size: 23px; line-height: 30px; color: var(--brand-gray);
    text-transform: uppercase;
  }
  .back-brand {
    position: absolute; right: 48px; top: 120px;
    font-family: 'Montserrat', sans-serif; font-weight: 700;
    font-size: 30px; color: var(--brand-blue); letter-spacing: 1px;
  }
  .holder { position: absolute; left: 40px; top: 330px; }
  .holder-name {
    font-family: 'Montserrat', sans-serif; font-weight: 700;
    font-size: 32px; color: var(--brand-blue); letter-spacing: 0.5px;
  }
  .holder-title {
    font-family: 'Open Sans', sans-serif; font-style: italic;
    font-size: 27px; color: var(--brand-gray); line-height: 30px;
  }
  .rule {
    position: absolute; left: 190px; right: 40px; top: 391px;
    height: 2px; background: var(--brand-blue);
  }
  .contact {
    position: absolute; left: 40px; top: 410px;
    font-family: 'Open Sans', sans-serif; font-size: 19px;
    line-height: 30px; color: var(--text-dark); letter-spacing: 0.5px;
  }
  .address {
    position: absolute; right: 40px; top: 410px; text-align: right;
    font-family: 'Open Sans', sans-serif; font-size: 19px;
    line-height: 30px; color: var(--text-dark); letter-spacing: 0.5px;
  }
  .address .dot { color: var(--brand-blue); padding: 0 6px; }
</style>
</head>
<body>
<main class="stage">

  <section class="card card-front">
    <svg class="card-band" viewBox="0 0 880 110" aria-hidden="true">
      <polygon points="0,0 880,0 880,62 0,118" fill="var(--soft-gray)" opacity="0.5"/>
      <polygon points="0,0 880,0 880,62 0,108" fill="var(--brand-gray)"/>
      <polygon points="0,0 880,0 880,62 0,78" fill="var(--brand-blue)"/>
    </svg>
    <div class="front-brand">CORVANE GROUP</div>
    <div class="front-web">www.corvanegroup.com</div>
  </section>

  <section class="card card-back">
    <svg class="card-band" viewBox="0 0 880 110" aria-hidden="true">
      <polygon points="0,0 880,0 880,72 0,8" fill="var(--soft-gray)" opacity="0.5"/>
      <polygon points="0,0 880,0 880,64 0,8" fill="var(--brand-gray)"/>
      <polygon points="0,0 880,0 880,38 0,8" fill="var(--brand-blue)"/>
      <polygon points="0,0 880,0 880,36 0,60" fill="var(--brand-blue)"/>
    </svg>
    <div class="tagline">Providing leadership<br>delivering success</div>
    <div class="back-brand">CORVANE GROUP</div>

    <div class="holder">
      <div class="holder-name">DANIEL R. WHITFORD</div>
      <div class="holder-title">President</div>
    </div>
    <div class="rule"></div>
    <div class="contact">
      1 (888) 555-0147<br>
      info@corvanegroup.com
    </div>
    <div class="address">
      4180 Harbor Point Lane<br>
      Tampa<span class="dot">•</span>Florida<span class="dot">•</span>33602
    </div>
  </section>

</main>
</body>
</html>
```